Heron Haulage needs Bussiness cards!

Our new trucking company needs business cards!
We need the same design with two different names and emails, everything else it's the same.
I have included our original logo so we can use it for the design.
Note: the logo to be used is the o e with the buffalo on the right side, next to the letters H and H.

Target Market(s)

Trucking, refrigerated transportation, freight

Industry/Entity Type

Business

Contact Information for Business Card

Card #1:
Marcus Whitfield
marcuswhitfield@heronhaulage.example
1-855-317-6094
(956)238-7160
4117 W. Larkin Ave.
Pharr, TX 78590
www.heronhaulage.example

Card#2:
Rosalba Quintero
rosalba@heronhaulage.example
1-855-317-6094
(956)238-7160
4117 W. Larkin Ave.
Pharr, TX 78590
www.heronhaulage.example

Font styles to use
Sans Serif

Colors
0655a3
ec1f27
ffffff

Requirements
Must have
• our logo
Nice to have
• roads on background,

```html
<!DOCTYPE html>
<html lang="en">
<head>
<meta charset="utf-8">
<title>Heron Haulage – Business Card</title>
<link rel="stylesheet" href="https://fonts.googleapis.com/css2?family=Exo+2:wght@300&family=Lato:wght@400;900&display=swap">
<style>
  :root {
    --brand-blue: #0655a3;
    --brand-red: #ec1f27;
    --white: #ffffff;
    --stage: #3d3d3d;
    --ink-muted: #8a8a8a;
    --card-w: 540px;
    --card-h: 309px;
  }
  * { box-sizing: border-box; margin: 0; padding: 0; }
  html, body { width: 1200px; height: 810px; overflow: hidden; }
  body {
    background: var(--stage);
    font-family: "Lato", sans-serif;
    display: flex;
    align-items: center;
    justify-content: center;
    gap: 40px;
  }
  .card {
    position: relative;
    width: var(--card-w);
    height: var(--card-h);
    border-radius: 18px;
    overflow: hidden;
  }

  /* Front */
  .card--front { background: var(--brand-blue); }
  .front__brand {
    position: absolute;
    left: 0; right: 0; top: 112px;
    display: flex;
    align-items: center;
    justify-content: center;
    gap: 14px;
  }
  .brand-dot {
    width: 34px; height: 34px;
    border-radius: 50%;
    background: var(--white);
    flex: none;
  }
  .front__brand .brand-name {
    font-weight: 900;
    font-size: 46px;
    color: var(--white);
    letter-spacing: 0.5px;
  }
  .front__url {
    position: absolute;
    left: 0; right: 0; bottom: 36px;
    text-align: center;
    color: var(--white);
    font-size: 13px;
  }

  /* Back */
  .card--back { background: var(--white); }
  .back__swoosh { position: absolute; inset: 0; width: 100%; height: 100%; }
  .back__brand {
    position: absolute;
    left: 28px; top: 96px;
    display: flex;
    align-items: center;
    gap: 8px;
  }
  .back__brand .brand-dot {
    width: 18px; height: 18px;
    background: var(--brand-blue);
  }
  .back__brand .brand-name {
    font-weight: 900;
    font-size: 22px;
    color: var(--brand-blue);
  }
  .back__name {
    position: absolute;
    left: 240px; top: 50px;
    font-family: "Exo 2", sans-serif;
    font-weight: 300;
    font-size: 20px;
    letter-spacing: 0.5px;
    color: var(--brand-red);
    text-transform: uppercase;
    white-space: nowrap;
  }
  .back__contact {
    position: absolute;
    left: 26px; bottom: 42px;
    list-style: none;
    font-size: 11px;
    line-height: 15px;
    color: var(--ink-muted);
  }
  .back__contact li { display: flex; align-items: center; gap: 6px; white-space: nowrap; }
  .back__contact svg { width: 10px; height: 10px; fill: var(--brand-red); flex: none; }
  .back__url {
    position: absolute;
    right: 20px; bottom: 80px;
    color: var(--white);
    font-size: 12px;
    white-space: nowrap;
  }
</style>
</head>
<body>

  <section class="card card--front">
    <div class="front__brand">
      <span class="brand-dot"></span>
      <span class="brand-name">Heron Haulage</span>
    </div>
    <p class="front__url">www.heronhaulage.example</p>
  </section>

  <section class="card card--back">
    <svg class="back__swoosh" viewBox="0 0 540 309" aria-hidden="true">
      <path d="M486 0 C466 130 346 295 76 309 L540 309 L540 0 Z" fill="var(--brand-red)"/>
      <path d="M495 0 C475 130 355 295 85 309 L540 309 L540 0 Z" fill="var(--white)"/>
      <path d="M500 0 C480 130 360 295 90 309 L540 309 L540 0 Z" fill="var(--brand-blue)"/>
    </svg>

    <div class="back__brand">
      <span class="brand-dot"></span>
      <span class="brand-name">Heron Haulage</span>
    </div>

    <h1 class="back__name">Marcus Whitfield</h1>

    <ul class="back__contact">
      <li>4117 W. Larkin Ave.</li>
      <li>Pharr, TX 78590</li>
      <li>
        <svg viewBox="0 0 24 24"><path d="M6.6 10.8a15.1 15.1 0 0 0 6.6 6.6l2.2-2.2c.3-.3.7-.4 1-.2 1.1.4 2.3.6 3.6.6.6 0 1 .4 1 1V20c0 .6-.4 1-1 1A17 17 0 0 1 3 4c0-.6.4-1 1-1h3.5c.6 0 1 .4 1 1 0 1.3.2 2.5.6 3.6.1.3 0 .7-.2 1z"/></svg>
        1-855-317-6094
      </li>
      <li>
        <svg viewBox="0 0 24 24"><path d="M7 1h10a2 2 0 0 1 2 2v18a2 2 0 0 1-2 2H7a2 2 0 0 1-2-2V3a2 2 0 0 1 2-2zm0 3v14h10V4z"/></svg>
        (956)238-7160
      </li>
      <li>
        <svg viewBox="0 0 24 24"><path d="M2 5h20v14H2zm2 2v.5l8 5 8-5V7l-8 5z"/></svg>
        marcuswhitfield@heronhaulage.example
      </li>
    </ul>

    <p class="back__url">www.heronhaulage.example</p>
  </section>

</body>
</html>
```